Healthy lifestyle Influencer business card

I need your creativity to have a business card that I can leave in all the restaurants, hotels and spas I visit to inform them that I am an influencer specializing in the wellness sector and that I will write a review about them. You can use my instagram photos Lunavita27 or on my website www.piattileggeriorto.it. I would like my business card to impress with its creativity! thank you very much!

Contact Information for Business Card

siteweb, instagram, phone number

Font styles to use
Decorative
Script

Colors
0094D4
00A9DD
6FCCEA
C7EBF8
E9F6FB
59FF00
82FF00
B8FF75
E3FFCB
F4FFEA
FFC000
F8CF3A
FAE287
FDF2CF
FEFAEE
F0912C
F2A743
F7CA91
FBE8D2
FDF5EE
EE7325
F08F49
F5BC92
FAE3D3
FDF4ED
EB3D1F
EC4F4E
F09395
F8D3D4
FCEDEE
E54698
E96AAD
F1A4CE
F9D9EA
FCEFF6

Requirements
Nice to have
• creativity

```html
<!DOCTYPE html>
<html lang="it">
<head>
<meta charset="utf-8">
<title>Orto Leggero – Biglietto da visita</title>
<link href="https://fonts.googleapis.com/css2?family=Allura&family=Questrial&family=Roboto:wght@300;400&display=swap" rel="stylesheet">
<style>
  :root {
    --page: #2b2b2b;
    --sage: #8fb3a7;
    --sage-deep: #7fa597;
    --sage-light: #a9c7bd;
    --ink: #3d3d3d;
    --band: #4a4a4a;
    --paper: #f4f4f3;
    --paper-shade: #e4e4e2;
    --contact: #f1f4f2;
    --kiwi: #7aa23a;
    --kiwi-light: #b8cf6a;
    --leaf: #3f8a3a;
  }
  * { margin: 0; padding: 0; box-sizing: border-box; }
  html, body { width: 1200px; height: 1138px; overflow: hidden; }
  body { background: var(--page); position: relative; font-family: "Questrial", sans-serif; }

  .card {
    position: absolute;
    width: 620px;
    height: 376px;
    border-radius: 16px;
    overflow: hidden;
  }
  .card--front { left: 272px; top: 184px; background: var(--sage); }
  .card--back { left: 274px; top: 606px; background: linear-gradient(180deg, var(--paper) 0%, var(--paper-shade) 100%); }

  .food-mosaic {
    position: absolute; inset: 0;
    background:
      radial-gradient(circle at 15% 20%, rgba(120,150,130,.35), transparent 22%),
      radial-gradient(circle at 60% 55%, rgba(150,180,160,.35), transparent 25%),
      radial-gradient(circle at 88% 82%, rgba(130,165,140,.35), transparent 22%),
      linear-gradient(135deg, var(--sage-light), var(--sage-deep));
  }

  .brand-name {
    position: absolute;
    font-family: "Questrial", sans-serif;
    font-weight: 400;
    color: var(--ink);
    white-space: nowrap;
    line-height: 1;
    letter-spacing: 1px;
  }
  .brand-tagline {
    position: absolute;
    font-family: "Questrial", sans-serif;
    color: var(--ink);
    white-space: nowrap;
    line-height: 1;
  }

  .card--front .brand-name { left: 0; width: 100%; text-align: center; top: 150px; font-size: 50px; }
  .card--front .brand-tagline { left: 0; width: 100%; text-align: center; top: 213px; font-size: 20px; }

  .social {
    position: absolute;
    display: flex; align-items: center; gap: 12px;
    font-family: "Roboto", sans-serif; font-weight: 400;
    color: var(--ink); font-size: 17px; line-height: 1;
  }
  .social__dot { width: 14px; height: 14px; border-radius: 50%; background: var(--ink); opacity: .75; }
  .card--front .social { left: 0; width: 100%; justify-content: center; top: 328px; }

  .card--back .brand-name { left: 22px; top: 70px; font-size: 50px; }
  .card--back .brand-tagline { left: 70px; top: 135px; font-size: 20px; }
  .person-name {
    position: absolute; left: 52px; top: 204px;
    font-family: "Allura", cursive; font-size: 40px; color: var(--ink); line-height: 1;
  }
  .card--back .social { left: 82px; top: 254px; }

  .kiwi-art {
    position: absolute; right: 0; top: 0; width: 130px; height: 165px;
    background: radial-gradient(ellipse at 85% 45%, var(--kiwi-light) 0%, var(--kiwi) 30%, var(--leaf) 55%, rgba(63,138,58,0) 72%);
  }

  .wave { position: absolute; left: 0; top: 0; width: 620px; height: 376px; }

  .contact {
    position: absolute; right: 34px; top: 272px;
    list-style: none;
    font-family: "Roboto", sans-serif; font-weight: 300;
    font-size: 17px; color: var(--contact);
  }
  .contact li { display: flex; justify-content: flex-end; align-items: center; gap: 12px; height: 24px; }
  .contact svg { width: 16px; height: 16px; fill: none; stroke: var(--contact); stroke-width: 1.6; }
</style>
</head>
<body>

<section class="card card--front" aria-label="Fronte del biglietto">
  <div class="food-mosaic" role="img" aria-label="Griglia di foto di piatti sani in tonalità verde salvia"></div>
  <div class="brand-name">Orto Leggero</div>
  <div class="brand-tagline">Leggerezza in ogni piatto</div>
  <div class="social"><span class="social__dot"></span>@Lunavita27</div>
</section>

<section class="card card--back" aria-label="Retro del biglietto">
  <div class="kiwi-art" role="img" aria-label="Kiwi tagliato a metà con foglie verdi"></div>

  <svg class="wave" viewBox="0 0 620 376" aria-hidden="true">
    <path d="M0,288 C90,332 190,352 300,318 C400,286 480,214 620,198 L620,214 C490,232 410,300 305,338 C200,374 90,360 0,326 Z" fill="var(--band)"/>
    <path d="M60,300 C150,330 240,336 330,306" stroke="var(--band)" stroke-width="3" fill="none"/>
    <path d="M0,338 C120,378 230,366 335,322 C435,280 505,242 620,232 L620,376 L0,376 Z" fill="var(--sage)"/>
  </svg>

  <div class="brand-name">Orto Leggero</div>
  <div class="brand-tagline">Leggerezza in ogni piatto</div>
  <div class="person-name">Luna Ferrante</div>
  <div class="social"><span class="social__dot"></span>@Lunavita27</div>

  <ul class="contact">
    <li>000-0000-0000
      <svg viewBox="0 0 16 16"><path d="M2 6 C2 3 14 3 14 6 L11 7 L10 5 L6 5 L5 7 Z M4 8 L12 8 L13 13 L3 13 Z"/></svg>
    </li>
    <li>www.piattileggeriorto.it
      <svg viewBox="0 0 16 16"><rect x="1.5" y="3.5" width="13" height="9"/><path d="M1.5 3.5 L8 9 L14.5 3.5"/></svg>
    </li>
    <li>info@piattileggeriorto.it
      <svg viewBox="0 0 16 16"><circle cx="8" cy="8" r="6.5"/><ellipse cx="8" cy="8" rx="3" ry="6.5"/><path d="M1.5 8 H14.5"/></svg>
    </li>
  </ul>
</section>

</body>
</html>
```